Logo and Card design for KRV Home Solutions LLC

I need an edgier logo and business card designs. Current logo attached. I like the colors below. I would like the logo to incorporate a home in the design.
Title = Principal-Acquisitions
Email:KRVHOMESOLUTIONS@fernmail.example
555-214-0937
facebook
IG
2 sided business card with the front being contact info a slogan about selling a home fast. The back incorporating What we do. Buy houses, land, or commercial property as is. We find solutions to make the process of selling simple and fair.

Target Market(s)

Motivated house sellers.

Industry/Entity Type

Business

Contact Information for Business Card

Who we are: We are a Faith based Real Estate Investment Company. We pay cash for homes in any condition and can close quick. Whatever the reason you need to sell fast, we can help. We believe in creating win-win solutions to help you in your time of need. We care! We can help!

Logo Text

KRV Home Solutions LLC

Font styles to use
Sans Serif

Colors
33a6d7
0355a3
85abd2
cee9f5
9d9d9d
b2b2b2
ffffff

Requirements
Must have
• Old logo attached. I want something edgier.
• Company name, phone number, description on the back of what we can do. Pay all cash. Buy in as is condition. No fees,Commisions or closing costs.Close quick. No hassles with solutions to meet your unique situation.
• Call today for an offer within 24 hours.

```html
<!DOCTYPE html>
<html lang="en">
<head>
<meta charset="utf-8">
<title>KRV Home Solutions – Business Card</title>
<link href="https://fonts.googleapis.com/css2?family=Lato:wght@400;700&display=swap" rel="stylesheet">
<style>
  :root {
    --stage: #333333;
    --paper: #ffffff;
    --slate: #7090a5;
    --slate-band: #6f8ea3;
    --slate-text: #6a8aa0;
    --ink: #4a4a4a;
    --navy: #2d4a60;
    --grey: #a7a9ab;
  }
  * { box-sizing: border-box; margin: 0; padding: 0; }
  html, body { width: 1200px; height: 900px; overflow: hidden; }
  body {
    background: var(--stage);
    font-family: "Lato", sans-serif;
    position: relative;
  }
  .card {
    position: absolute;
    top: 306px;
    height: 271px;
    background: var(--paper);
    box-shadow: 3px 3px 6px rgba(0,0,0,.55);
    overflow: hidden;
  }
  .card--front { left: 149px; width: 439px; }
  .card--back  { left: 608px; width: 441px; }

  /* front */
  .accent { position: absolute; left: 0; top: 117px; }
  .brand {
    position: absolute; left: 222px; top: 92px;
    display: flex; align-items: center; gap: 8px;
    color: var(--slate-text); font-weight: 700; font-size: 21px;
    letter-spacing: .3px; text-transform: uppercase;
  }
  .brand__mark { width: 14px; height: 14px; background: var(--slate-text); }
  .person { position: absolute; left: 33px; top: 122px; }
  .person__name { color: var(--slate-text); font-weight: 700; font-size: 17px; text-transform: uppercase; }
  .person__title { color: var(--ink); font-size: 13px; margin-top: 1px; }
  .contact { position: absolute; left: 31px; top: 176px; color: var(--ink); list-style: none; }
  .contact li { display: flex; align-items: center; gap: 5px; line-height: 18px; }
  .contact__phone { font-size: 14.5px; }
  .contact__email { font-size: 12.5px; }
  .contact svg { fill: var(--slate); flex: none; }
  .band {
    position: absolute; left: 0; bottom: 0; width: 100%; height: 45px;
    background: var(--slate-band); color: var(--paper);
    display: flex; align-items: center; justify-content: center;
    font-weight: 700; font-size: 12.5px; text-transform: uppercase;
  }

  /* back */
  .pitch {
    position: absolute; left: 0; top: 0; width: 100%; height: 215px;
    background: var(--slate); color: var(--paper);
    padding: 20px 0 0 38px;
  }
  .pitch__lead { font-weight: 700; font-size: 14.5px; margin-bottom: 3px; }
  .pitch__needs { list-style: none; font-weight: 700; font-size: 14.5px; line-height: 20px; margin-bottom: 5px; }
  .pitch__needs li::before { content: "●"; font-size: 11px; margin-right: 5px; vertical-align: 1px; }
  .pitch__points p { font-size: 14.5px; line-height: 20px; }
  .cta {
    position: absolute; left: 0; bottom: 0; width: 100%; height: 56px;
    display: flex; flex-direction: column; align-items: center; justify-content: center;
    color: var(--navy); font-weight: 700; font-size: 15px; text-transform: uppercase; line-height: 20px;
  }
</style>
</head>
<body>
  <section class="card card--front">
    <svg class="accent" width="27" height="36" viewBox="0 0 27 36" aria-hidden="true">
      <polygon points="0,0 10,0 10,36 0,36" fill="var(--grey)"/>
      <polygon points="13,0 26,0 26,36 19,36" fill="var(--slate)"/>
    </svg>
    <div class="brand"><span class="brand__mark"></span>KRV Home Solutions</div>
    <div class="person">
      <p class="person__name">Marcus Hale</p>
      <p class="person__title">Managing Director</p>
    </div>
    <ul class="contact">
      <li class="contact__phone">
        <svg width="10" height="10" viewBox="0 0 10 10" aria-hidden="true"><path d="M1 3q4-3 8 0l-1 2-2-1v-1H4v1L2 5zM2 6h6v3H2z"/></svg>
        555-214-0937
      </li>
      <li class="contact__email">
        <svg width="10" height="8" viewBox="0 0 10 8" aria-hidden="true"><path d="M0 0h10v8H0z M1 1l4 3 4-3" stroke="#fff" stroke-width=".8"/></svg>
        krvhomesolutions@fernmail.example
      </li>
    </ul>
    <div class="band">Call today to get an all cash offer within 24 hours</div>
  </section>

  <section class="card card--back">
    <div class="pitch">
      <p class="pitch__lead">KRV Home Solutions can help with your unique situation.</p>
      <ul class="pitch__needs">
        <li>Need Cash?</li>
        <li>Need to sell your house fast?</li>
        <li>Vacant house?</li>
      </ul>
      <div class="pitch__points">
        <p>We make selling your house easy!</p>
        <p>We buy houses, land or commercial property as is.</p>
        <p>We pay cash and cover all closing costs.</p>
        <p>We make the repairs so you don't have to.</p>
        <p>Close fast and move on with your life!</p>
      </div>
    </div>
    <div class="cta">
      <span>Call or text today to hear our cash offer!</span>
      <span>555-214-0937</span>
    </div>
  </section>
</body>
</html>
```